Online Advice via Video Site requires Cutting Edge Homepage

We need a creative new and exciting webdesign for our tutoring via video-chat website.

We have prepared a "demo" homepage for you to see various promotional material that we think would be suitable for the homepage. http://www.quillmarsh.com/demo

The actual site is undergoing some final tinkering but can be accessed and used at http://www.quillmarsh.com

There is NO NEED to take any colours or design structure from this.

We expect the logo to be changed to match the new site. The new logo should match the site's function.

I have included some other projects that we like the look of:
http://www.vantoplex.com.au/design/143762
http://www.vantoplex.com.au/design/561630
http://www.vantoplex.com.au/design/247199
http://www.vantoplex.com.au/design/255195
http://www.birchlume.tv/

Target Market(s)

People that will work as tutors/advisers or be student/clients

Industry/Entity Type

Tutoring

Requirements
Must have
• The search is the main feature of the homepage

After the search the next goal of the page is to get people to sign up to the site

Login, (optional inclusion of the gablenet login - if you don't include it then you need only have a "login" button... no username or password input fields)

Footer
Nice to have
• The promotional material for the site, the colours on the Prezi file CAN BE changed to suit the new design you propose.

```html
<!DOCTYPE html>
<html lang="en">
<head>
<meta charset="utf-8">
<title>Quill Marsh — Online Advice</title>
<link rel="stylesheet" href="https://fonts.googleapis.com/css2?family=Source+Sans+3:ital,wght@0,300;0,400;0,600;1,400&display=swap">
<style>
:root{
  --ink:#4f4f4f;
  --ink-soft:#6a6a6a;
  --blue:#3a68c8;
  --blue-soft:#4f7fcf;
  --btn:#4e80d6;
  --btn-dark:#3463b8;
  --dark:#2b2b2b;
  --band:#e7e7e7;
  --header:#f1f1f1;
  --panel-line:#e2e6e7;
  --footer-area:#f3f3f3;
  --tab:#e4e4e4;
  --tab-active:#cfcfcf;
}
*{box-sizing:border-box;margin:0;padding:0}
html,body{width:1145px;height:1200px;overflow:hidden;background:#fff}
body{font-family:"Source Sans 3",sans-serif;color:var(--ink)}
.stage{position:relative;width:1050px;height:1100px;transform:scale(1.0905);transform-origin:0 0;background:#fff}
.abs{position:absolute}

/* top bar */
.topbar{left:0;top:0;width:1050px;height:64px;background:var(--dark)}
.social-login{left:470px;top:12px;width:160px;height:26px;background:var(--btn);border:1px solid #6b97dd;border-radius:2px;color:#fff;font-size:11px;line-height:24px}
.social-login .mark{position:absolute;left:0;top:0;width:26px;height:24px;border-right:1px solid #6b97dd}
.social-login .mark i{position:absolute;left:9px;top:8px;width:8px;height:8px;background:#fff;border-radius:50%}
.social-login span{position:absolute;left:40px}
.field{top:13px;height:25px;background:#fff;border:1px solid #ccc;border-radius:2px;font-size:11px;font-style:italic;color:#aaa;padding-left:8px;line-height:23px}
.login-btn{left:934px;top:13px;width:65px;height:24px;background:var(--btn);border:1px solid #7aa3e0;border-radius:2px;color:#1d2f55;font-size:12px;line-height:22px;padding-left:28px}
.login-btn svg{position:absolute;left:7px;top:3px}
.forgot{left:849px;top:43px;font-size:10px;font-style:italic;color:#c9c9c9;text-decoration:underline}

/* header */
.header-bg{left:0;top:64px;width:1050px;height:294px;background:linear-gradient(180deg,#f7f7f7,var(--header))}
.search-band{left:0;top:358px;width:1050px;height:60px;background:var(--band)}
.brand{left:43px;top:82px;font-size:40px;font-weight:300;color:var(--ink-soft);letter-spacing:.5px}
.connect{left:727px;top:97px;font-size:13px;color:var(--ink)}
.net{top:93px;width:25px;height:25px;border-radius:2px}

.nav{left:55px;top:151px;display:flex;gap:4px}
.nav a{display:block;height:33px;line-height:33px;padding:0 13px;background:var(--tab);color:var(--ink);font-size:13px;text-decoration:none;border-radius:2px 2px 0 0}
.nav a.active{background:linear-gradient(180deg,#e9eef0,#d6dfe2);padding:0 18px;color:#333}

/* hero */
.hero{left:43px;top:183px;width:646px;height:310px;background:#fff;box-shadow:0 3px 6px rgba(0,0,0,.25)}
.hero-img{left:6px;top:6px;width:634px;height:298px;background:linear-gradient(90deg,#fbfcfd 0%,#eef2f6 45%,#c8d6e4 75%,#aec0d2 100%)}
.hero-quote{left:43px;top:68px;font-size:16px;line-height:22px;color:#5a5a5a;width:360px}
.hero-now{left:43px;top:112px;font-size:23px;color:var(--blue)}
.slider-ctrl{left:12px;top:276px;width:36px;height:22px;background:#7a7a7a;border-radius:2px}

/* panels */
.panel{background:#fff;box-shadow:0 2px 5px rgba(0,0,0,.2)}
.panel-inner{position:absolute;inset:5px;border:1px solid var(--panel-line)}
.panel-title{font-size:18px;color:var(--blue)}
.search-panel{left:703px;top:184px;width:296px;height:159px}
.checks{left:24px;top:66px;font-size:11px;color:#666;display:flex;gap:14px}
.checks label{display:flex;align-items:center;gap:5px}
.checks i{width:8px;height:8px;border:1px solid #aaa;background:#eee;display:inline-block}
.search-input{left:14px;top:96px;width:269px;height:33px;border:1px solid #c8c8c8;border-radius:5px;background:linear-gradient(180deg,#f0f0f0,#fafafa)}
.adv-search{left:819px;top:381px;font-size:11px;color:#555;text-decoration:underline}
.search-btn{left:918px;top:375px;width:67px;height:27px;background:linear-gradient(180deg,var(--btn),var(--btn-dark));border-radius:3px;color:#fff;font-size:15px;text-align:center;line-height:26px}

.advisors-panel{left:710px;top:443px;width:282px;height:325px}
.adv-list{left:30px;top:68px;font-size:12.5px;line-height:22px;color:#444;list-style:none}
.adv-list li::before{content:"•";color:#888;margin-right:6px}
.adv-list li.sub{padding-left:18px}

/* welcome */
.welcome-h{left:43px;top:516px;font-size:21px;color:var(--blue)}
.welcome-p{left:42px;top:552px;width:648px;font-size:12.4px;line-height:18px;text-align:justify;color:#555}
.points{left:96px;top:657px;list-style:none}
.points li{font-size:15px;font-style:italic;color:var(--blue-soft);height:31px;padding-left:20px;position:relative}
.points li::before{content:"";position:absolute;left:2px;top:5px;border-left:7px solid #6f95d6;border-top:5px solid transparent;border-bottom:5px solid transparent}

/* lower section */
.lower-bg{left:0;top:796px;width:1050px;height:244px;background:var(--footer-area);border-top:2px solid #ddd}
.ftabs{left:42px;top:798px;display:flex;font-size:13px;color:#555}
.ftabs span{height:32px;line-height:32px;padding:0 8px}
.ftabs span.active{background:var(--tab-active);color:#333;padding:0 12px}
.fbullet{font-size:13px;color:#444}
.fbullet::before{content:"•";color:#888;margin-right:7px}
.rule{left:42px;top:921px;width:645px;height:1px;background:#bfbfbf}
.topics-box{left:52px;top:945px;width:108px;height:73px;background:var(--btn);color:#fff;font-size:12.5px;text-align:center;padding-top:20px;line-height:15px;border-radius:2px}
.topics-box::after{content:"";position:absolute;right:-12px;top:25px;border-left:12px solid var(--btn);border-top:11px solid transparent;border-bottom:11px solid transparent}
.topic{font-size:13px;color:#444}
.vdivider{left:703px;top:808px;width:2px;height:218px;background:#cfcfcf}
.testi-title{left:757px;top:808px;font-size:18px;color:var(--blue)}
.quote{left:720px;width:265px;font-size:12.4px;line-height:18px;font-style:italic;color:#555}
.quote b{font-size:18px;font-style:normal;font-weight:400;color:#666;line-height:0}
.author{left:940px;width:45px;text-align:right;font-size:12.5px;font-weight:600;color:#444}

.footer{left:0;top:1040px;width:1050px;height:60px;background:var(--dark);color:#bdbdbd;font-size:11px;text-align:center;line-height:58px}
</style>
</head>
<body>
<div class="stage">

  <!-- top bar -->
  <div class="abs topbar"></div>
  <div class="abs social-login"><div class="mark"><i></i></div><span>sign in with gablenet</span></div>
  <div class="abs field" style="left:665px;width:130px">Username</div>
  <div class="abs field" style="left:799px;width:130px">Password</div>
  <div class="abs login-btn">
    <svg width="16" height="16" viewBox="0 0 16 16"><circle cx="8" cy="5" r="4" fill="#1d2f55"/><path d="M1 16c0-4 3-6 7-6s7 2 7 6z" fill="#1d2f55"/></svg>
    Log in
  </div>
  <div class="abs forgot">Forgot password</div>

  <!-- header -->
  <div class="abs header-bg"></div>
  <div class="abs search-band"></div>
  <div class="abs brand">Quill Marsh</div>
  <div class="abs connect">Connect with us :</div>
  <div class="abs net" style="left:829px;background:#3b5b9a"></div>
  <div class="abs net" style="left:864px;background:#2aa1dc"></div>
  <div class="abs net" style="left:899px;background:#f08a1c"></div>
  <div class="abs net" style="left:934px;background:#3a3a3a"></div>

  <nav class="abs nav">
    <a class="active">Home</a><a>About us</a><a>Our Services</a><a>Advisors</a><a>Testimonials</a><a>Contact us</a>
  </nav>

  <!-- hero -->
  <div class="abs hero">
    <div class="abs hero-img" role="img" aria-label="Photo of a woman with outstretched arms on a sunny beach"></div>
    <div class="abs hero-quote">"Imagine if, whenever you had a problem you could instantly access the world's experts to solve it.</div>
    <div class="abs hero-now" style="top:114px">Now you can!"</div>
    <div class="abs slider-ctrl">
      <svg width="36" height="22" viewBox="0 0 36 22"><path d="M15 6v10l-7-5z" fill="#fff"/><path d="M21 6v10l7-5z" fill="#fff"/><rect x="17.5" y="3" width="1" height="16" fill="#999"/></svg>
    </div>
  </div>

  <!-- search panel -->
  <div class="abs panel search-panel">
    <div class="panel-inner"></div>
    <svg class="abs" style="left:16px;top:18px" width="34" height="30" viewBox="0 0 34 30"><circle cx="12" cy="12" r="9" fill="#eef4fa" stroke="#8ea0b2" stroke-width="2.5"/><path d="M19 18l11 9" stroke="#7a7a7a" stroke-width="4" stroke-linecap="round"/></svg>
    <div class="abs panel-title" style="left:56px;top:20px">Search</div>
    <div class="abs checks"><label><i></i>Topics</label><label><i></i>Advisors</label></div>
    <div class="abs search-input"></div>
  </div>
  <div class="abs adv-search">Advanced Search</div>
  <div class="abs search-btn">Search</div>

  <!-- advisors panel -->
  <div class="abs panel advisors-panel">
    <div class="panel-inner"></div>
    <div class="abs" style="left:20px;top:12px;width:30px;height:30px;border-radius:4px;background:linear-gradient(180deg,#e7a65a,#3c3c46)" role="img" aria-label="Advisor icon"></div>
    <div class="abs panel-title" style="left:58px;top:18px">Advisors</div>
    <ul class="abs adv-list">
      <li>Teach the topics you know well</li>
      <li>Educate people in your spare time</li>
      <li class="sub">Answer single questions</li>
      <li class="sub">Provide ongoing tutoring</li>
      <li>Work when it suits you</li>
      <li class="sub">Pre-book appointments</li>
      <li class="sub">Answer questions only when you can</li>
      <li>Earn money for your time</li>
      <li class="sub">Set your own fee rate</li>
    </ul>
  </div>

  <!-- welcome -->
  <h1 class="abs welcome-h" style="font-weight:400">Welcome to our site</h1>
  <p class="abs welcome-p">Sed ut perspiciatis unde omnis iste natus error sit voluptatem accusantium doloremque laudantium, totam rem aperiam, eaque ipsa quae ab illo inventore veritatis et quasi architecto beatae vitae dicta sunt explicabo. Nemo enim ipsam voluptatem quia voluptas sit aspernatur aut odit aut fugit, sed quia consequuntur magni dolores eos qui ratione voluptatem sequi nesciunt. Neque porro quisquam est, qui dolorem ipsum quia dolor sit amet, consectetur, adipisci velit, sed quia non numquam eius modi tempora incidunt ut laboreet.</p>
  <ul class="abs points">
    <li>QuillMarsh is the place for e-learning, mentoring &amp; professional advice</li>
    <li>It instantly connects people with knowledge and those who need it</li>
    <li>Connects people for ongoing advice or on off answers</li>
    <li>Ask questions and/or work exactly when it suits you</li>
  </ul>

  <!-- lower section -->
  <div class="abs lower-bg"></div>
  <div class="abs ftabs">
    <span>Instant Personal Advice</span>
    <span style="margin-left:16px">Direct Video Conference</span>
    <span style="margin-left:14px">Advisors and/or Clients</span>
    <span class="active" style="margin-left:9px">Coinvale or Credt Card</span>
  </div>
  <div class="abs fbullet" style="left:89px;top:846px">Charges based on individual advisor's rate</div>
  <div class="abs fbullet" style="left:416px;top:846px">Pay only for the time you use</div>
  <div class="abs fbullet" style="left:89px;top:878px">Pay via coinvale or credit card</div>
  <div class="abs fbullet" style="left:416px;top:878px">Be paid via credit card</div>
  <div class="abs rule"></div>

  <div class="abs topics-box">ADVISORS<br>BY TOPICS</div>
  <div class="abs topic" style="left:193px;top:955px">English</div>
  <div class="abs topic" style="left:297px;top:955px">Building</div>
  <div class="abs topic" style="left:432px;top:955px">Cultural Studies</div>
  <div class="abs topic" style="left:598px;top:955px">Criminology</div>
  <div class="abs topic" style="left:193px;top:985px">Agriculture</div>
  <div class="abs topic" style="left:294px;top:985px">Veterinary Science</div>

  <div class="abs vdivider"></div>
  <div class="abs" style="left:718px;top:806px;width:24px;height:28px;background:linear-gradient(180deg,#f4f4f4,#d8dde2);border:1px solid #b8bec4" role="img" aria-label="Notepad icon"></div>
  <div class="abs testi-title">Testimonials</div>
  <p class="abs quote" style="top:862px"><b>“</b> Neque porro quisquam est, qui dolorem ipsum quia dolor sit amet, consectetur, adipisci velit, sed quia non numquam eius modi <b>”</b></p>
  <div class="abs author" style="top:923px">David</div>
  <p class="abs quote" style="top:952px"><b>“</b> Neque porro quisquam est, qui dolorem ipsum quia dolor sit amet, consectetur, adipisci velit, sed quia non numquam eius modi <b>”</b></p>
  <div class="abs author" style="top:1013px">David</div>

  <footer class="abs footer">Copyright &nbsp;© 2012 www.quillmarsh,com &nbsp; All rights reserved</footer>
</div>
</body>
</html>
```